Re-design and craft the perfect CV platform

We are building a CV-based platform designed to connect employees and employers, with a strong focus on individual users. As we're just starting out, we're looking to have our platform and logo redesigned to better reflect our vision
https://app.zelvorhire.com/
Colors like in the logo attached
#87C032 #6A6E71 #618930 - also you can add more colors if you like.
https://app.zelvorhire.com/dashboard - This page would be nice if you plan it, like personal Bio dashboard. Attached picture (Dashboard wanted) one idea from how we would like to be, but we are open for new professional ideas/solutions.
https://app.zelvorhire.com/posts - On this page we want to be showed the jobs posted. Attached one picture about our idea (jobs page wanted)
https://app.zelvorhire.com/profile - design something nice.
Only Photoshop, Illustrator or Figma
Other pictures from the app attached (as looking right now)

Target Market(s)

Job seekers, HR, Recruiters

Industry/Entity Type

HR Tech

Number of Pages Required

5+ page

Colors
00AB8E
00BBA5
67D7C9
C6EFE9
E9F9F6

```html
<!DOCTYPE html>
<html lang="en">
<head>
<meta charset="utf-8">
<title>Zelvorhire – Recruitment Web App Screens</title>
<link href="https://fonts.googleapis.com/css2?family=Montserrat:wght@400;500;600;700;800&display=swap" rel="stylesheet">
<style>
:root{
  --green:#87C032;
  --green-dark:#618930;
  --green-soft:#eef6e2;
  --gray:#6A6E71;
  --ink:#2f3234;
  --board:#3a3d40;
  --panel-dark:#404346;
  --line:#e3e5e6;
  --muted:#a2a6a8;
  --white:#ffffff;
}
*{box-sizing:border-box;margin:0;padding:0}
html,body{width:1200px;height:2220px;overflow:hidden}
body{background:var(--board);font-family:"Montserrat",Arial,sans-serif;color:var(--ink);position:relative}
.backdrop{position:absolute;inset:0}
.section-title{position:absolute;left:72px;color:var(--white);font-weight:800;font-size:40px;letter-spacing:1px}
.screen{position:absolute;left:72px;width:1056px;background:var(--white);border-radius:18px;overflow:hidden;box-shadow:0 18px 40px rgba(0,0,0,.35)}

/* ---------- login ---------- */
.login{top:176px;height:496px;display:flex}
.login-aside{width:330px;background:var(--panel-dark);border-radius:18px;color:var(--white);display:flex;flex-direction:column;align-items:center;justify-content:center;padding:0 34px;text-align:center}
.brand{display:flex;align-items:center;gap:10px}
.brand-dot{width:34px;height:34px;border-radius:50%;background:var(--green)}
.brand-name{font-weight:800;font-size:30px;color:var(--white);letter-spacing:1px}
.login-aside .tag{margin-top:14px;font-weight:700;font-size:13px;letter-spacing:.5px}
.login-aside .lead{margin-top:6px;font-size:13px;font-weight:500}
.login-aside .fine{margin-top:10px;font-size:11px;line-height:1.5;color:#d6d8d9}
.login-aside .fine b{color:var(--green);font-weight:600}
.login-main{flex:1;position:relative;padding:88px 0 0 84px}
.btn-outline{position:absolute;top:22px;right:28px;border:1.5px solid var(--green);color:var(--green-dark);font-size:10px;font-weight:700;padding:7px 12px;border-radius:4px}
.login-main h1{font-size:30px;font-weight:800;color:var(--ink)}
.login-main .sub{font-size:12px;color:var(--gray);margin-top:4px}
.field{margin-top:26px;width:380px}
.field label{display:flex;justify-content:space-between;font-size:11px;font-weight:700;color:var(--gray)}
.field label span{font-weight:500;color:var(--muted)}
.field .input{margin-top:8px;height:34px;border:1px solid var(--line);border-radius:4px;background:#fafafa}
.remember{margin-top:18px;display:flex;align-items:center;gap:8px;font-size:11px;color:var(--gray);font-weight:600}
.check{width:14px;height:14px;border:1.5px solid var(--green);border-radius:3px}
.actions{margin-top:18px;display:flex;align-items:center;gap:20px}
.btn-green{background:var(--green);color:var(--white);font-weight:700;font-size:12px;padding:10px 26px;border-radius:5px}
.actions .alt{font-size:11px;color:var(--gray);font-weight:600}
.arcs{position:absolute;right:0;bottom:0}

/* ---------- shared app shell ---------- */
.app{display:flex}
.sidebar{width:230px;padding:26px 20px;border-right:1px solid var(--line)}
.sidebar .brand-dot{width:26px;height:26px}
.sidebar .brand-name{color:var(--ink);font-size:20px}
.portrait{margin:20px auto 12px;width:120px;height:132px;border-radius:10px;background:linear-gradient(160deg,#c9ccce,#8e9396)}
.person{text-align:center;font-weight:800;font-size:15px}
.role{text-align:center;font-size:11px;color:var(--green-dark);font-weight:600;margin-top:2px}
.mail{text-align:center;font-size:10px;color:var(--gray);margin-top:2px}
.facts{margin-top:16px;font-size:10px}
.facts div{display:flex;justify-content:space-between;padding:5px 0;border-bottom:1px solid #f0f1f1}
.facts dt{color:var(--muted);font-weight:600}
.facts dd{color:var(--ink);font-weight:600}
.side-note{margin-top:12px;font-size:10px;font-weight:700;color:var(--ink)}
.side-note span{display:block;font-weight:500;color:var(--gray);margin-top:3px}
.topbar{height:66px;display:flex;align-items:center;justify-content:space-between;padding:0 26px;border-bottom:1px solid var(--line)}
.topbar h2{font-size:18px;font-weight:800}
.top-tools{display:flex;align-items:center;gap:16px;font-size:11px;font-weight:700;color:var(--gray)}
.avatar{width:34px;height:34px;border-radius:50%;background:#b8bcbe;border:2px solid var(--green)}
.card-label{font-size:11px;font-weight:800;color:var(--ink);letter-spacing:.3px}
.small{font-size:10px;color:var(--gray);line-height:1.5}

/* ---------- dashboard ---------- */
.dashboard{top:800px;height:624px}
.dash-main{flex:1;display:flex;flex-direction:column}
.dash-body{flex:1;display:flex;gap:22px;padding:18px 26px}
.dash-col{flex:1;display:flex;flex-direction:column;gap:14px}
.about{background:var(--green);border-radius:10px;padding:16px 18px;color:var(--white)}
.about .card-label{color:var(--white);font-size:13px}
.about p{font-size:11px;line-height:1.55;margin-top:6px}
.pair{display:flex;gap:18px}
.pair>div{flex:1}
.jobs-mini{border:1px solid var(--line);border-radius:10px;padding:12px 14px}
.tabs{display:flex;gap:18px;font-size:10px;font-weight:700;color:var(--muted);margin:8px 0}
.tabs .on{color:var(--green-dark);border-bottom:2px solid var(--green)}
.mini-row{display:flex;align-items:center;gap:10px;padding:8px 0;border-top:1px solid #f0f1f1}
.mini-logo{width:24px;height:24px;border-radius:50%;background:var(--green-soft);border:1.5px solid var(--green)}
.mini-row .txt{flex:1;font-size:10px;color:var(--gray)}
.mini-row .txt b{color:var(--ink);display:block}
.pill{font-size:9px;font-weight:700;padding:5px 10px;border-radius:4px;background:var(--green);color:var(--white)}
.pill.grey{background:#e8eaeb;color:var(--gray)}
.dash-right{width:200px;display:flex;flex-direction:column;gap:14px}
.box{border:1px solid var(--line);border-radius:10px;padding:12px 14px}
.list{list-style:none;margin-top:6px}
.list li{font-size:10px;color:var(--gray);padding:2px 0 2px 12px;position:relative}
.list li::before{content:"";position:absolute;left:0;top:7px;width:5px;height:5px;border-radius:50%;background:var(--green)}
.lang{margin-top:8px;font-size:10px;color:var(--gray);font-weight:600}
.bar{height:6px;background:#eceeef;border-radius:3px;margin-top:4px}
.bar i{display:block;height:100%;background:var(--green);border-radius:3px}

/* ---------- jobs ---------- */
.jobs{top:1560px;height:620px}
.jobs-main{flex:1;display:flex;flex-direction:column}
.jobs-tools{display:flex;align-items:center;gap:10px;padding:16px 26px}
.search{flex:1;height:32px;border:1px solid var(--line);border-radius:5px;font-size:10px;color:var(--muted);display:flex;align-items:center;padding-left:12px}
.tool{width:32px;height:32px;border:1px solid var(--line);border-radius:5px}
.tool.on{background:var(--green);border-color:var(--green)}
table{width:calc(100% - 52px);margin:0 26px;border-collapse:collapse;font-size:10px}
th{text-align:left;font-weight:800;color:var(--ink);padding:10px 8px;background:#f5f6f6;font-size:10px}
td{padding:10px 8px;border-bottom:1px solid #f0f1f1;color:var(--gray);vertical-align:middle}
.pos{display:flex;align-items:center;gap:10px}
.pos b{display:block;color:var(--ink)}
.status{background:var(--green-soft);color:var(--green-dark);font-weight:700;padding:4px 9px;border-radius:4px;font-size:9px}
.date{background:#f1f2f2;padding:4px 9px;border-radius:4px}
.jobs-foot{margin-top:auto;display:flex;justify-content:space-between;align-items:center;padding:16px 26px;font-size:10px;color:var(--gray)}
.pager{display:flex;gap:6px}
.pager span{width:22px;height:22px;border:1px solid var(--line);border-radius:4px;display:flex;align-items:center;justify-content:center;font-size:9px}
.pager .on{background:var(--green);color:var(--white);border-color:var(--green)}
</style>
</head>
<body>

<svg class="backdrop" width="1200" height="2220" aria-hidden="true">
  <polygon points="760,0 1200,0 1200,260" fill="#87C032"/>
  <polygon points="980,0 1200,0 1200,120" fill="#618930"/>
  <polygon points="0,700 0,980 240,700" fill="#87C032"/>
  <polygon points="1200,1300 1200,1620 900,1620" fill="#87C032"/>
  <polygon points="0,1460 0,1700 180,1460" fill="#618930"/>
  <polygon points="1200,2000 1200,2220 960,2220" fill="#618930"/>
</svg>

<div class="section-title" style="top:100px">LOGIN</div>
<section class="screen login">
  <aside class="login-aside">
    <div class="brand"><span class="brand-dot"></span><span class="brand-name">ZELVORHIRE</span></div>
    <div class="tag">RECRUITMENT WEB APP ACCESS</div>
    <div class="lead">Create an account or sign in</div>
    <p class="fine">By creating an account or signing in you understand and agree to Zelvorhire Terms. You also acknowledge our <b>Cookie</b> and <b>Privacy policies</b>.</p>
  </aside>
  <div class="login-main">
    <span class="btn-outline">CREATE ACCOUNT</span>
    <h1>LOGIN INTO ZELVORHIRE</h1>
    <p class="sub">Enter your login details below</p>
    <div class="field"><label>ENTER YOUR EMAIL ADDRESS</label><div class="input"></div></div>
    <div class="field"><label>PASSWORD <span>Forgot your password</span></label><div class="input"></div></div>
    <div class="remember"><span class="check"></span>REMEMBER ME</div>
    <div class="actions"><span class="btn-green">SIGN IN →</span><span class="alt">DON'T HAVE AN ACCOUNT?</span></div>
    <svg class="arcs" width="240" height="240" aria-hidden="true">
      <circle cx="240" cy="240" r="90" fill="none" stroke="#eceeef" stroke-width="2"/>
      <circle cx="240" cy="240" r="140" fill="none" stroke="#eceeef" stroke-width="2"/>
      <circle cx="240" cy="240" r="190" fill="none" stroke="#eceeef" stroke-width="2"/>
    </svg>
  </div>
</section>

<div class="section-title" style="top:732px">DASHBOARD</div>
<section class="screen dashboard app">
  <aside class="sidebar">
    <div class="brand"><span class="brand-dot"></span><span class="brand-name">ZELVORHIRE</span></div>
    <div class="portrait" role="img" aria-label="Profile photo of the candidate"></div>
    <div class="person">DANA WHITFIELD</div>
    <div class="role">Software Engineer</div>
    <div class="mail">dana.whitfield@mailbox.test</div>
    <dl class="facts">
      <div><dt>Phone</dt><dd>+00 123 456 789</dd></div>
      <div><dt>Date of birth</dt><dd>12.04.1994</dd></div>
      <div><dt>Age</dt><dd>30</dd></div>
      <div><dt>Nationality</dt><dd>Irish</dd></div>
      <div><dt>Location</dt><dd>Dublin</dd></div>
    </dl>
    <div class="side-note">Right to Work &amp; Education<span>Full right to work, no visa needed</span></div>
    <div class="side-note">Work Experience<span>7 years in software delivery</span></div>
  </aside>
  <div class="dash-main">
    <div class="topbar"><h2>ZELVORHIRE DASHBOARD</h2><div class="top-tools"><span>ENG ▾</span><span>🔔</span><span class="avatar"></span></div></div>
    <div class="dash-body">
      <div class="dash-col">
        <div class="about">
          <div class="card-label">ABOUT ME</div>
          <p>Experienced and collaborative software engineer with over 7 years in the tech industry, skilled in developing innovative solutions for complex problems. With a focus on efficiency, user experience, and reliability, I thrive on teamwork and continuous learning.</p>
        </div>
        <div class="pair">
          <div><div class="card-label">WORK EXPERIENCE</div><p class="small">7 years of experience in IT</p></div>
          <div><div class="card-label">DRIVER'S LICENSE</div><p class="small">Licence type: Full, Category B</p></div>
        </div>
        <div>
          <div class="card-label">EDUCATION</div>
          <p class="small">• Qualification: Honours Bachelor in Computer Science<br>• Institution: Northgate Institute of Technology, 2016<br>• Additional Certifications: Cloud Practitioner, Agile Scrum Master</p>
        </div>
        <div class="jobs-mini">
          <div class="card-label">MY JOBS</div>
          <div class="tabs"><span>SAVED JOBS</span><span class="on">APPLIED JOBS</span><span>INTERVIEW JOBS</span></div>
          <div class="mini-row"><span class="mini-logo"></span><div class="txt"><b>Web Developer</b>Applied on 14 May · Remote role, full time position</div><span class="pill grey">DETAILS</span><span class="pill">APPLY</span></div>
          <div class="mini-row"><span class="mini-logo"></span><div class="txt"><b>Product Manager</b>Applied on 02 June · Hybrid role in Dublin office</div><span class="pill grey">DETAILS</span><span class="pill">APPLY</span></div>
        </div>
      </div>
      <div class="dash-right">
        <div class="box">
          <div class="card-label">SKILLS</div>
          <ul class="list"><li>Python, Java, JavaScript</li><li>Agile team delivery</li><li>Cloud deployments</li><li>REST API design</li><li>Code reviews</li><li>Unit and load testing</li></ul>
        </div>
        <div class="box">
          <div class="card-label">HOBBIES &amp; INTERESTS</div>
          <ul class="list"><li>Reading novels</li><li>Hiking trails</li><li>Cooking</li><li>Photography</li></ul>
        </div>
        <div class="box">
          <div class="card-label">LANGUAGES</div>
          <div class="lang">English<div class="bar"><i style="width:95%"></i></div></div>
          <div class="lang">Spanish<div class="bar"><i style="width:65%"></i></div></div>
          <div class="lang">German<div class="bar"><i style="width:40%"></i></div></div>
        </div>
      </div>
    </div>
  </div>
</section>

<div class="section-title" style="top:1492px">JOBS</div>
<section class="screen jobs app">
  <aside class="sidebar">
    <div class="brand"><span class="brand-dot"></span><span class="brand-name">ZELVORHIRE</span></div>
    <div class="portrait" role="img" aria-label="Profile photo of the candidate"></div>
    <div class="person">DANA WHITFIELD</div>
    <div class="role">Software Engineer</div>
    <div class="mail">dana.whitfield@mailbox.test</div>
    <dl class="facts">
      <div><dt>Phone</dt><dd>+00 123 456 789</dd></div>
      <div><dt>Date of birth</dt><dd>12.04.1994</dd></div>
      <div><dt>Age</dt><dd>30</dd></div>
      <div><dt>Nationality</dt><dd>Irish</dd></div>
      <div><dt>Location</dt><dd>Dublin</dd></div>
    </dl>
    <div class="side-note">Right to Work &amp; Education<span>Full right to work, no visa needed</span></div>
    <div class="side-note">Work Experience<span>7 years in software delivery</span></div>
  </aside>
  <div class="jobs-main">
    <div class="topbar"><h2>JOBS</h2><div class="top-tools"><span>ENG ▾</span><span>🔔</span><span class="avatar"></span></div></div>
    <div class="jobs-tools"><div class="search">Enter Keyword</div><span class="tool"></span><span class="tool on"></span><span class="tool"></span><span class="tool"></span></div>
    <table>
      <thead><tr><th>JOB POSITION</th><th>COMPANY</th><th>STATUS</th><th>FOLLOW UP</th><th>DATE APPLIED</th><th></th></tr></thead>
      <tbody>
        <tr><td><div class="pos"><span class="mini-logo"></span><div><b>Northbeam Labs</b>Software Engineer</div></div></td><td>Northbeam Labs<br>Dublin</td><td><span class="status">APPLIED</span></td><td><span class="date">06/03/2025</span></td><td><span class="date">28/02/2025</span></td><td><span class="pill">VIEW</span></td></tr>
        <tr><td><div class="pos"><span class="mini-logo"></span><div><b>Harbor Ledger</b>Operations Manager</div></div></td><td>Harbor Ledger<br>Cork</td><td><span class="status">APPLIED</span></td><td><span class="date">10/03/2025</span></td><td><span class="date">01/03/2025</span></td><td><span class="pill">VIEW</span></td></tr>
        <tr><td><div class="pos"><span class="mini-logo"></span><div><b>Quillstone Systems</b>QA Engineer</div></div></td><td>Quillstone Systems<br>Galway</td><td><span class="status">APPLIED</span></td><td><span class="date">12/03/2025</span></td><td><span class="date">03/03/2025</span></td><td><span class="pill">VIEW</span></td></tr>
        <tr><td><div class="pos"><span class="mini-logo"></span><div><b>Vantora Analytics</b>Data Analyst</div></div></td><td>Vantora Analytics<br>Limerick</td><td><span class="status">APPLIED</span></td><td><span class="date">15/03/2025</span></td><td><span class="date">05/03/2025</span></td><td><span class="pill">VIEW</span></td></tr>
        <tr><td><div class="pos"><span class="mini-logo"></span><div><b>Ferncloud Works</b>Cloud Engineer</div></div></td><td>Ferncloud Works<br>Dublin</td><td><span class="status">APPLIED</span></td><td><span class="date">18/03/2025</span></td><td><span class="date">08/03/2025</span></td><td><span class="pill">VIEW</span></td></tr>
        <tr><td><div class="pos"><span class="mini-logo"></span><div><b>Marlow Studio</b>UI Designer</div></div></td><td>Marlow Studio<br>Remote</td><td><span class="status">APPLIED</span></td><td><span class="date">20/03/2025</span></td><td><span class="date">11/03/2025</span></td><td><span class="pill">VIEW</span></td></tr>
      </tbody>
    </table>
    <div class="jobs-foot"><span>Show full page ▾</span><div class="pager"><span>‹</span><span>1</span><span>2</span><span>3</span><span class="on">4</span><span>5</span><span>6</span><span>›</span></div></div>
  </div>
</section>

</body>
</html>
```